Global (re)insurance broker needs a business card design

We need a classic business card for our company that is headquartered in SG, with offices in Malaysia and Dubai. We specialise in insurance and reinsurance broking and consultancy for our global clients.

```html
<!DOCTYPE html>
<html lang="en">
<head>
<meta charset="utf-8">
<title>Norvane – Business Card</title>
<link href="https://fonts.googleapis.com/css2?family=Open+Sans:wght@400;600;700&display=swap" rel="stylesheet">
<style>
  :root {
    --stage: #2b2b2e;
    --card: #1f1e23;
    --card-back: #1c1c20;
    --brand-blue: #24479a;
    --brand-green: #c3dcb7;
    --text-light: #f2f2f2;
    --emboss: #111114;
  }
  html, body {
    margin: 0;
    padding: 0;
    width: 1200px;
    height: 780px;
    overflow: hidden;
    background: var(--stage);
    font-family: "Open Sans", Arial, sans-serif;
  }
  .canvas {
    position: relative;
    width: 1200px;
    height: 780px;
  }
  .card {
    position: absolute;
    top: 235px;
    width: 540px;
    height: 310px;
    overflow: hidden;
    box-shadow: 0 14px 30px rgba(0,0,0,0.45);
  }
  .card--front { left: 40px; background: var(--card); }
  .card--back { left: 620px; background: var(--card-back); }

  .card__art { position: absolute; inset: 0; }

  .brand-name {
    position: absolute;
    margin: 0;
    font-weight: 700;
    letter-spacing: 1px;
    line-height: 1;
  }
  .card--front .brand-name {
    top: 44px;
    left: 190px;
    font-size: 54px;
    color: var(--brand-green);
  }
  .card--back .brand-name {
    top: 120px;
    left: 0;
    width: 100%;
    text-align: center;
    font-size: 64px;
    color: var(--emboss);
  }

  .person {
    position: absolute;
    top: 128px;
    left: 34px;
  }
  .person__name {
    margin: 0;
    font-size: 30px;
    font-weight: 700;
    line-height: 1.05;
  }
  .person__first { color: var(--brand-blue); }
  .person__last { color: var(--brand-green); }
  .person__title {
    margin: 4px 0 0;
    font-size: 14px;
    color: var(--text-light);
  }

  .divider {
    position: absolute;
    left: 236px;
    top: 140px;
    width: 2px;
    height: 68px;
    background: var(--text-light);
  }

  .contact {
    position: absolute;
    left: 252px;
    top: 140px;
    margin: 0;
    padding: 0;
    list-style: none;
    font-size: 13.5px;
    color: var(--text-light);
  }
  .contact__item {
    display: flex;
    align-items: center;
    gap: 8px;
    height: 22px;
  }
  .contact__icon { width: 12px; height: 12px; flex: none; }

  .address {
    position: absolute;
    left: 24px;
    bottom: 10px;
    margin: 0;
    font-size: 12px;
    line-height: 1.2;
    color: var(--text-light);
    white-space: nowrap;
  }
</style>
</head>
<body>
<main class="canvas">

  <section class="card card--front" aria-label="Business card front">
    <svg class="card__art" width="540" height="310" viewBox="0 0 540 310" aria-hidden="true">
      <path class="band" d="M0 212 C 200 247, 420 264, 520 310 L0 310 Z" fill="var(--brand-blue)"/>
      <path class="band-line" d="M0 199 C 200 234, 420 250, 528 302" fill="none" stroke="var(--brand-green)" stroke-width="3" stroke-linecap="round"/>
    </svg>

    <p class="brand-name">NORVANE</p>

    <div class="person">
      <h1 class="person__name"><span class="person__first">Mira</span> <span class="person__last">Lestari</span></h1>
      <p class="person__title">Chief Operating Officer</p>
    </div>

    <div class="divider"></div>

    <ul class="contact">
      <li class="contact__item">
        <svg class="contact__icon" viewBox="0 0 12 12"><rect x="3" y="0.5" width="6" height="11" rx="1" fill="none" stroke="var(--text-light)" stroke-width="1"/><circle cx="6" cy="9.6" r="0.7" fill="var(--text-light)"/></svg>
        +65 9000 4126
      </li>
      <li class="contact__item">
        <svg class="contact__icon" viewBox="0 0 12 12"><circle cx="6" cy="6" r="5.5" fill="var(--brand-blue)"/><path d="M1 6h10M6 0.5v11M6 0.5q-3 5.5 0 11M6 0.5q3 5.5 0 11" fill="none" stroke="var(--text-light)" stroke-width="0.6"/></svg>
        www.norvane.com
      </li>
      <li class="contact__item">
        <svg class="contact__icon" viewBox="0 0 12 12"><rect x="0.5" y="2.5" width="11" height="7.5" fill="none" stroke="var(--text-light)" stroke-width="1"/><path d="M0.5 2.5 6 7l5.5-4.5" fill="none" stroke="var(--text-light)" stroke-width="1"/></svg>
        mira@norvane.com
      </li>
    </ul>

    <p class="address">22 Harbour Lane, Meridian Tower #08-14, Singapore 018906</p>
  </section>

  <section class="card card--back" aria-label="Business card back">
    <p class="brand-name">NORVANE</p>
  </section>

</main>
</body>
</html>
```